Colin Vardek Business card

Hey there, I’m hoping to have a business card designed. I’m in Real estate and just switched to a new Brokerage called: The Harbourline Property Group

The back could just be the company name maybe or whatever looks good!

I’ve attached some logos of our company and some cards my buddy had done up.

On the card:
Colin Vardek
colinvardek@mailora.com
587-412-9065
colinvardek.ca

Target Market(s)

Home buyers and sellers

Industry/Entity Type

Real Estate

Contact Information for Business Card

just looking for a cool and modern design with my picture on it. I like the idea of Black and red being used.

Requirements
Must have
• all the details provided. I'm open to anything. Just want a professional looking card.

```html
<!DOCTYPE html>
<html lang="en">
<head>
<meta charset="UTF-8">
<title>Colin Vardek – Business Card</title>
<link rel="stylesheet" href="https://fonts.googleapis.com/css2?family=Poppins:wght@300;400;600;800&display=swap">
<style>
  :root {
    --stage: #222222;
    --card: #1f1f23;
    --red: #d0223c;
    --white: #ffffff;
    --ink-soft: #2b2b30;
    --photo-a: #e9e6e3;
    --photo-b: #3a3436;
  }
  * { box-sizing: border-box; margin: 0; padding: 0; }
  html, body {
    width: 1200px; height: 780px; overflow: hidden;
    background: var(--stage);
    font-family: "Poppins", sans-serif;
  }
  .canvas {
    position: relative; width: 1200px; height: 780px;
    display: flex; align-items: center; justify-content: center; gap: 50px;
  }
  .card {
    position: relative; width: 540px; height: 309px;
    background: var(--card);
    border-radius: 4px;
    overflow: hidden;
    box-shadow: 0 18px 40px rgba(0,0,0,.55);
  }

  /* Front */
  .brand {
    position: absolute; right: 34px; top: 58px; width: 260px;
    text-align: right; color: var(--white);
    font-weight: 800; font-size: 26px; line-height: 1.05; letter-spacing: -.5px;
    text-transform: uppercase;
  }
  .brand .keep { white-space: nowrap; }
  .brand-mark {
    display: inline-block; width: 9px; height: 9px;
    background: var(--red); border-radius: 50%; margin-left: 6px; vertical-align: middle;
  }
  .band {
    position: absolute; left: 0; right: 0; top: 152px; height: 78px;
    background: var(--red);
  }
  .identity {
    position: absolute; left: 30px; top: 164px; width: 190px; color: var(--white);
    white-space: nowrap;
  }
  .identity .name { font-size: 24px; line-height: 1.1; font-weight: 300; }
  .identity .name strong { font-weight: 600; }
  .identity .title { font-size: 12px; font-weight: 400; margin-top: 3px; }
  .portrait {
    position: absolute; left: 228px; top: 143px; width: 96px; height: 96px;
    border-radius: 50%; border: 3px solid var(--card);
    box-shadow: 0 0 0 2px var(--red);
    background: radial-gradient(circle at 50% 40%, var(--photo-a) 0 55%, var(--photo-b) 100%);
  }
  .contact {
    position: absolute; left: 340px; top: 169px; color: var(--white);
    font-size: 13px; font-weight: 400; list-style: none; white-space: nowrap;
  }
  .contact li { display: flex; align-items: center; gap: 8px; line-height: 22px; }
  .contact svg { width: 12px; height: 12px; fill: var(--white); flex: none; }
  .website {
    position: absolute; left: 86px; top: 252px;
    color: var(--red); font-size: 15px; font-weight: 300;
  }

  /* Back */
  .card-back .brand-emboss {
    position: absolute; inset: 0; display: flex; align-items: center; justify-content: center;
    text-align: center; color: var(--ink-soft);
    font-weight: 800; font-size: 40px; line-height: 1.02; text-transform: uppercase;
    letter-spacing: -.5px; padding: 0 60px;
  }
</style>
</head>
<body>
<main class="canvas">
  <section class="card card-front" aria-label="Business card front">
    <div class="brand">The Harbourline Property <span class="keep">Group<span class="brand-mark"></span></span></div>
    <div class="band"></div>
    <div class="identity">
      <p class="name"><strong>Colin</strong> Vardek</p>
      <p class="title">Managing Director</p>
    </div>
    <div class="portrait" role="img" aria-label="Portrait photo of Colin Vardek"></div>
    <ul class="contact">
      <li>
        <svg viewBox="0 0 24 24" aria-hidden="true"><path d="M6.6 10.8a15.1 15.1 0 0 0 6.6 6.6l2.2-2.2a1 1 0 0 1 1-.25 11.4 11.4 0 0 0 3.6.57 1 1 0 0 1 1 1V20a1 1 0 0 1-1 1A17 17 0 0 1 3 4a1 1 0 0 1 1-1h3.5a1 1 0 0 1 1 1c0 1.25.2 2.45.57 3.57a1 1 0 0 1-.25 1z"/></svg>
        587-412-9065
      </li>
      <li>
        <svg viewBox="0 0 24 24" aria-hidden="true"><path d="M3 5h18a1 1 0 0 1 1 1v12a1 1 0 0 1-1 1H3a1 1 0 0 1-1-1V6a1 1 0 0 1 1-1zm9 7.2L4 7.3V17h16V7.3z"/></svg>
        colinvardek@mailora.com
      </li>
    </ul>
    <p class="website">www.colinvardek.ca</p>
  </section>

  <section class="card card-back" aria-label="Business card back">
    <div class="brand-emboss">The Harbourline Property Group</div>
  </section>
</main>
</body>
</html>
```